Edgey, Modern Air Conditioning Website

Bramble Works
current website - www.kelvaroom.nz
Friendloop - www.facebook.com/bramwrk

We really have no idea about webdesign etc we are Engineers not Graphic artists or creative writers. We really just want a edgy, modern website completed on our behalf

We can get pictures of projects as directed or happy for you to use stock images of Talvoro Mecha NZ (Heatpumps) air conditioning and exposed ducting etc

we would like the website to be heavily based on the below website. I like what they have done with both the site and the app but obviously would need to suit Bramble Works, snowflakes heating cooling etc etc Blue and white to match our logo etc

http://parrowbeams.co.nz/

Need links to contact page:
Bramble Works
27 Harlow Crescent
Petone
Wellington

0800 529 174 (0800BRAMWKS)

Marta.k@bramwks.co.nz

BRAMBLE WORKS
SATISFACTION GAURANTEED

WHY CHOOSE BRAMBLE WORKS
EXPERIENCE COUNTS

We have a team of nationally trained and qualified Refrigeration/HVAC/Electrical Engineers and Technicians based in Petone, Wellington offering services to Wellington, Manuwatu and the Wairarapa. We are factory trained and authorised to design, service and install all major brands including Talvoro, Pelnor, Korrowane Electric, Veltrada and Osmelo units. We extend our installation warranty to match that of the manufacturer’s warranty and specialise in our own diagnostics and repair.

SATISFACTION GUARANTEE
We aim to please and I put my name behind our brand! We will take care of your project from start to finish and offer a unique experience with our 100% satisfaction Guarantee*. We will supply and install your system and if your system is not installed how it was explained or not up to a trades standard we will return to make any the necessary modifications free of charge. We back this service up with our 0% upfront strategy, the power is in your hands. We will only invoice you once the installation has been completed up to a BRAMBLE WORKS standard.

LOW PRESSURE SALES
Nobody likes the vacuum salesmen’s techniques and neither do we. We will come to your home or business to provide a free measure and quote. Our experience will insure this is a quick and painless experience, you will be provided with expert advice from a qualified Refrigeration Engineer, not a car salesmen turned “Heating Guru”. We will follow up with an email providing our best price straight up, installation details and online brochures. We won’t bug you with repeated phone calls and inbox clogging emails. Once we receive confirmation we will issue you with an installation date and typically have your installation completed within 10 working days.

BRANDS
www.talvoromecha.co.nz
www.pelnor.co.nz
http://quellaro.co.nz/

SERVICES
Heatpumps/Air Conditioning – Heat pumps are the most efficient way of using electricity to heat your home, but some are more efficient than others. We will select the right model for your requirements taking into account the capacity required, the visual impact of the system, the style of system, air flow and obviously your personal preferences. We only install the highest quality brands that offer outstanding after sales support. Cassettes, Consoles, Under Ceilings, Ducted, Hiwalls, Multis… Confused? Give us a call.

COMMERCIAL
We have a growing Portfolio of clients that rely on us for their Commercial requirements. We have proven ourselves to be a force to be reckoned with to be able to think outside the square and come up with unique and cost effective solutions to heat and cool large areas.

CENTRAL HEATING
Ducted Heatpumps are the holy grail of central heating and guess what? They can also cool and dehumidify your home. Ducted Heatpumps are often overlooked or priced out of reach by less experienced salesmen as its not just a point and shoot approach. We pride ourselves in our work with Ducted systems, we are able to provide quick and economic quotations and can provide expert advice on all the extra options on Ducted systems with zone control, fresh air integration, positive pressure solutions. We use the best materials when it comes to insulated ducting, mounting equipment, drainage materials. Every system we design is designed with the lowest possible decibel reading, least amount of static pressure and maximum effieciency with the help of the very latest software available.

VENTILATION
Home ventilation is a very important part of insuring you have a nice dry home to maximise the efficiency of your Heat pump. Whilst HRV systems are not designed to Heat your house they are designed to keep it dry, provide fresh filtered air to ensure your home healthy and easy to heat. We offer a number of solutions from integrated ducted heatpump systems to balanced heat recovery systems and positive air systems.

TESTIMONIALS
http://www.lotbazaro.co.nz/Browse/Listing.aspx?id=415728306

Target Market(s)

Home Owners

Industry/Entity Type

Air Conditioning

Colors
33a6d7
ffffff

Requirements
Must have
• Could possibly use the 'O' from Bramble Works logo throughout website - see business Card
Nice to have
• Bright & Crisp - White and Blue
• Would love to have our Logo used throughout the website.

```html
<!DOCTYPE html>
<html lang="en">
<head>
<meta charset="utf-8">
<title>Bramble Works – Heat Pumps &amp; Air Conditioning</title>
<link rel="stylesheet" href="https://fonts.googleapis.com/css2?family=Raleway:ital,wght@0,400;0,500;0,600;0,700;0,800;1,400&display=swap">
<style>
:root{
  --blue:#33a6d7;
  --blue-dark:#2a86b8;
  --navy:#253847;
  --footer:#1f3447;
  --band:#2b80b0;
  --ink:#2b2b2b;
  --muted:#6d6d6d;
  --line:#d8d8d8;
  --soft:#f6f6f6;
  --white:#ffffff;
}
*{box-sizing:border-box;margin:0;padding:0}
html,body{width:1200px;height:2922px;overflow:hidden}
body{font-family:"Raleway",sans-serif;color:var(--ink);background:var(--white);position:relative}
.abs{position:absolute}

/* header */
.site-header{position:absolute;left:0;top:0;width:1200px;height:121px;background:var(--white)}
.brand{position:absolute;left:82px;top:20px;font-size:40px;font-weight:800;color:var(--blue);letter-spacing:1px;line-height:1}
.brand-sub{position:absolute;left:84px;top:72px;font-size:13px;font-weight:500;color:#8a8a8a;letter-spacing:10px}
.top-contact{position:absolute;top:18px;display:flex;align-items:center;gap:12px;font-size:18px;color:#333}
.top-contact .dot{width:34px;height:34px;border-radius:50%;background:var(--blue);display:flex;align-items:center;justify-content:center}
.main-nav{position:absolute;left:485px;top:70px;width:635px;height:45px;border-bottom:1px solid var(--line)}
.main-nav a{position:absolute;top:13px;font-size:15px;font-weight:700;color:#333;text-decoration:none;letter-spacing:.3px}
.main-nav a.active{color:var(--blue)}

/* hero */
.hero{position:absolute;left:0;top:121px;width:1200px;height:522px;background:linear-gradient(135deg,#eef1f2 0%,#d9d3c8 45%,#c7b9a6 70%,#e9e6e1 100%)}
.hero-arrow{position:absolute;top:225px}
.hero-caption{position:absolute;left:0;bottom:0;width:1200px;height:49px;background:rgba(30,30,30,.72);color:var(--white);font-size:24px;font-weight:600;text-align:center;line-height:49px}

/* section titles */
.section-title{position:absolute;left:0;width:1200px;text-align:center;font-size:28px;font-weight:700;color:#222;letter-spacing:.5px}
.section-title span{color:var(--blue)}
.divider{position:absolute;left:342px;width:516px;height:20px}

/* welcome */
.welcome-text{position:absolute;left:80px;top:785px;width:1040px;text-align:center;font-size:14.5px;line-height:25px;color:#444}
.btn{position:absolute;background:var(--blue);color:var(--white);font-size:13px;font-weight:700;text-align:center;border-radius:2px}

/* services band */
.services{position:absolute;left:0;top:1009px;width:1200px;height:413px}
.service{position:absolute;top:0;width:300px;height:413px;text-align:center;color:var(--white)}
.service h3{position:absolute;top:187px;left:0;width:100%;font-size:21px;font-weight:700;letter-spacing:.5px}
.service p{position:absolute;top:229px;left:35px;width:230px;font-size:13.5px;line-height:22px;font-weight:600;height:88px;overflow:hidden}
.service .more{position:absolute;top:343px;left:93px;width:116px;height:33px;background:var(--white);font-size:13px;font-weight:700;line-height:33px;border-radius:2px}
.service.light .more{color:var(--blue)}
.service.dark .more{color:var(--navy)}
.service svg.icon{position:absolute;top:43px;left:92px}

/* gallery */
.gallery-item{position:absolute;top:1574px;width:253px;height:176px}

/* testimonials / why */
.split{position:absolute;left:0;top:1808px;width:1200px;height:432px;background:var(--soft)}
.col-title{position:absolute;top:45px;font-size:27px;font-weight:700;color:#222}
.col-title span{color:var(--blue)}
.col-rule{position:absolute;top:93px;height:1px;background:var(--line)}
.quote{position:absolute;left:228px;top:124px;width:330px;font-style:italic;font-size:15px;line-height:27px;color:#333}
.client-name{position:absolute;left:228px;top:310px;font-size:19px;font-weight:600;color:var(--blue)}
.client-role{position:absolute;left:228px;top:338px;font-size:13px;color:#333}
.reason{position:absolute;left:744px;width:380px}
.reason h4{font-size:15.5px;font-weight:700;color:#222;margin-bottom:8px}
.reason p{font-size:13px;line-height:22px;color:#555}
.reason p b{color:var(--blue);font-weight:500}

/* brands */
.brand-box{position:absolute;top:2396px;width:152px;height:70px;border:1px solid #dcdcdc;background:var(--white);display:flex;align-items:center;justify-content:center;font-size:17px;font-weight:700;color:#333}

/* newsletter */
.newsletter{position:absolute;left:0;top:2513px;width:1200px;height:78px;background:var(--band)}
.newsletter h5{position:absolute;left:193px;top:23px;font-size:27px;font-weight:600;color:var(--white)}
.news-input{position:absolute;left:496px;top:19px;width:382px;height:40px;background:var(--white);font-size:13px;color:#444;padding:12px 10px}
.news-btn{position:absolute;left:892px;top:19px;width:195px;height:40px;background:var(--navy);color:var(--white);font-size:18px;font-weight:700;letter-spacing:1.5px;text-align:center;line-height:40px}

/* footer */
.site-footer{position:absolute;left:0;top:2591px;width:1200px;height:284px;background:var(--footer);color:#cfd8e0}
.foot-title{position:absolute;top:46px;font-size:17px;font-weight:700;color:var(--white);letter-spacing:.5px}
.foot-title span{color:var(--blue)}
.foot-rule{position:absolute;top:75px;width:110px;height:1px;background:#3d5468}
.foot-list{position:absolute;top:92px;list-style:none;font-size:14px;line-height:31px}
.foot-list li::before{content:"›";color:var(--blue);margin-right:8px}
.foot-list li.active{color:var(--white);font-weight:700}
.foot-contact{position:absolute;left:321px;top:92px;font-size:14px;line-height:20px}
.foot-contact .row{display:flex;align-items:center;gap:10px;margin-top:16px}
.field{position:absolute;left:668px;width:227px;height:30px;background:var(--white);font-size:12px;color:#888;padding:8px}
.social{position:absolute;left:1005px;display:flex;align-items:center;gap:14px;font-size:13px;font-weight:700;color:var(--white)}
.social i{width:30px;height:30px;border-radius:50%;background:var(--blue-dark);display:block}
.copyright{position:absolute;left:0;top:2875px;width:1200px;height:47px;background:var(--blue);color:var(--white);font-size:13px;font-weight:600;text-align:center;line-height:47px}
</style>
</head>
<body>

<header class="site-header">
  <div class="brand">BRAMBLE</div>
  <div class="brand-sub">WORKS</div>
  <div class="top-contact" style="left:735px">
    <span class="dot"><svg width="16" height="16" viewBox="0 0 24 24"><path d="M6.6 10.8a15 15 0 0 0 6.6 6.6l2.2-2.2a1 1 0 0 1 1-.25 11.4 11.4 0 0 0 3.6.57 1 1 0 0 1 1 1V20a1 1 0 0 1-1 1A17 17 0 0 1 3 4a1 1 0 0 1 1-1h3.5a1 1 0 0 1 1 1c0 1.25.2 2.45.57 3.6a1 1 0 0 1-.25 1z" fill="#fff"/></svg></span>
    022 481 3906
  </div>
  <div class="top-contact" style="left:910px">
    <span class="dot"><svg width="16" height="16" viewBox="0 0 24 24"><rect x="3" y="6" width="18" height="12" rx="1" fill="none" stroke="#fff" stroke-width="2"/><path d="M3 7l9 6 9-6" fill="none" stroke="#fff" stroke-width="2"/></svg></span>
    Marta.k@bramwks.co.nz
  </div>
  <nav class="main-nav">
    <a class="active" style="left:20px">HOME</a>
    <a style="left:123px">ABOUT US</a>
    <a style="left:252px">OUR SERVICES</a>
    <a style="left:415px">PROJECT</a>
    <a style="left:538px">CONTACT US</a>
  </nav>
</header>

<section class="hero" role="img" aria-label="Family relaxing in a bright living room with a wall-mounted heat pump">
  <svg class="hero-arrow" style="left:60px" width="22" height="40" viewBox="0 0 22 40"><path d="M18 4L4 20l14 16" fill="none" stroke="#fff" stroke-width="3"/></svg>
  <svg class="hero-arrow" style="left:1118px" width="22" height="40" viewBox="0 0 22 40"><path d="M4 4l14 16L4 36" fill="none" stroke="#fff" stroke-width="3"/></svg>
  <div class="hero-caption">We have installed thousands of heat pumps and also specialise in diagnostics and repairs</div>
</section>

<h1 class="section-title" style="top:685px">WELCOME TO <span>BRAMBLE WORKS</span></h1>
<svg class="divider" style="top:736px" viewBox="0 0 516 20"><line x1="0" y1="10" x2="238" y2="10" stroke="#c8c8c8"/><line x1="278" y1="10" x2="516" y2="10" stroke="#c8c8c8"/><circle cx="258" cy="10" r="8" fill="none" stroke="#c8c8c8" stroke-width="2" stroke-dasharray="3 2"/></svg>
<p class="welcome-text">Purchasing a Heatpump or Ventilation System can be a significant investment but it doesnt have to be a daunting one.<br>We have a team of nationally trained and qualified Refrigeration/HVAC and Electricians. We are factory trained and authorised to service and install all major<br>brands including Talvoro, Lumigo, Pelnor and Korrowane Electric, Veltrada and Osmelo units. We have installed thousands of heat pumps<br>and also specialise in diagnostics and repairs.</p>
<div class="btn" style="left:538px;top:919px;width:124px;height:38px;line-height:38px">Read More »</div>

<section class="services">
  <svg class="abs" style="left:0;top:0" width="1200" height="413" viewBox="0 0 1200 413">
    <rect width="1200" height="413" fill="#3aa6d8"/>
    <polygon points="340,0 560,0 600,40 600,373 560,413 340,413 300,373 300,40" fill="#253847"/>
    <polygon points="940,0 1200,0 1200,413 940,413 900,373 900,40" fill="#2c3f4e"/>
    <polygon points="600,40 640,0 860,0 900,40 900,373 860,413 640,413 600,373" fill="#3d98c9"/>
  </svg>
  <div class="service light" style="left:0">
    <svg class="icon" width="116" height="116" viewBox="0 0 116 116"><circle cx="58" cy="58" r="56" fill="#fff"/><circle cx="58" cy="58" r="38" fill="#3aa6d8"/><rect x="38" y="48" width="40" height="14" rx="2" fill="#fff"/><path d="M44 68v6M52 68v6M60 68v6M68 68v6" stroke="#fff" stroke-width="2"/></svg>
    <h3>AIR CONDITIONING</h3>
    <p>Heat pumps are the most efficient way of using electricity to heat your home, but some are more efficient</p>
    <div class="more">Read More »</div>
  </div>
  <div class="service dark" style="left:300px">
    <svg class="icon" width="116" height="116" viewBox="0 0 116 116"><circle cx="58" cy="58" r="56" fill="#fff"/><circle cx="58" cy="58" r="38" fill="#253847"/><rect x="44" y="40" width="28" height="36" fill="#fff"/><path d="M50 46h5M61 46h5M50 54h5M61 54h5M50 62h5M61 62h5" stroke="#253847" stroke-width="3"/></svg>
    <h3>COMMERCIAL</h3>
    <p>We have a growing Portfolio of clients that rely on us for their Commercial requirements. We have proven ourselves to</p>
    <div class="more">Read More »</div>
  </div>
  <div class="service light" style="left:600px">
    <svg class="icon" width="116" height="116" viewBox="0 0 116 116"><circle cx="58" cy="58" r="56" fill="#fff"/><circle cx="58" cy="58" r="38" fill="#3d98c9"/><path d="M42 48v26M50 48v26M58 48v26M66 48v26M74 48v26" stroke="#fff" stroke-width="5" stroke-linecap="round"/><path d="M38 56h40M38 68h40" stroke="#fff" stroke-width="2"/></svg>
    <h3>CENTRAL HEATING</h3>
    <p>Ducted Heatpumps are the holy grail of central heating and guess what? They can also cool and dehumidify your</p>
    <div class="more">Read More »</div>
  </div>
  <div class="service dark" style="left:900px">
    <svg class="icon" width="116" height="116" viewBox="0 0 116 116"><circle cx="58" cy="58" r="56" fill="#fff"/><circle cx="58" cy="58" r="38" fill="#2c3f4e"/><circle cx="58" cy="58" r="5" fill="#fff"/><path d="M58 53c-4-10 2-16 8-14 4 2 2 8-8 14zM63 58c10-4 16 2 14 8-2 4-8 2-14-8zM58 63c4 10-2 16-8 14-4-2-2-8 8-14zM53 58c-10 4-16-2-14-8 2-4 8-2 14 8z" fill="#fff"/></svg>
    <h3>VENTILATION</h3>
    <p>Home ventilation is a very important part of insuring you have a nice dry home to maximise the efficiency of</p>
    <div class="more">Read More »</div>
  </div>
</section>

<h2 class="section-title" style="top:1462px">PROJECT <span>GALLERY</span></h2>
<svg class="divider" style="top:1504px" viewBox="0 0 516 20"><line x1="0" y1="10" x2="516" y2="10" stroke="#c8c8c8"/></svg>
<div class="gallery-item" style="left:80px;background:linear-gradient(160deg,#f1ece6,#cdbfae)" role="img" aria-label="Living room with heat pump installation"></div>
<div class="gallery-item" style="left:343px;background:linear-gradient(160deg,#f4f4f4,#c9cdd1)" role="img" aria-label="Radiator thermostat valve being adjusted"></div>
<div class="gallery-item" style="left:606px;background:linear-gradient(160deg,#f5f5f2,#7a6c60)" role="img" aria-label="Bedroom with installed heating system"></div>
<div class="gallery-item" style="left:867px;background:linear-gradient(160deg,#f7f7f7,#c4c8cc)" role="img" aria-label="Ceiling cassette air conditioning unit"></div>

<section class="split">
  <h2 class="col-title" style="left:82px">CLIENT <span>TESTIMONIALS</span></h2>
  <div class="col-rule" style="left:82px;width:480px"></div>
  <svg class="abs" style="left:598px;top:100px" width="2" height="310"><line x1="1" y1="0" x2="1" y2="310" stroke="#cfcfcf" stroke-dasharray="4 4"/></svg>
  <svg class="abs" style="left:78px;top:128px" width="120" height="120" viewBox="0 0 120 120"><circle cx="60" cy="60" r="58" fill="#fff" stroke="#33a6d7" stroke-width="2"/><circle cx="60" cy="60" r="50" fill="#b7c4cf" role="img" aria-label="Client portrait"/></svg>
  <svg class="abs" style="left:226px;top:112px" width="28" height="24" viewBox="0 0 28 24"><rect x="0" y="0" width="10" height="24" fill="#dcdcdc"/><rect x="15" y="0" width="10" height="24" fill="#dcdcdc"/></svg>
  <p class="quote">&nbsp;&nbsp;&nbsp;&nbsp;&nbsp;&nbsp;Lorem ipsum dolor sit amet, consectetuer adipiscing elit, sed diam nonummy nibh euismod tincidunt ut laoreet dolore magna aliquam erat volutpat. Ut wisi enim ad minim veniam, quis nostrud exerci tation ullamcorper suscipit lobortis nisl ut aliquip</p>
  <div class="client-name">Elsa Varnhold</div>
  <div class="client-role">Marketing Manager</div>

  <h2 class="col-title" style="left:647px">WHY CHOOSE <span>BRAMBLE WORKS</span></h2>
  <div class="col-rule" style="left:647px;width:475px"></div>
  <svg class="abs" style="left:682px;top:100px" width="2" height="300"><line x1="1" y1="0" x2="1" y2="300" stroke="#bcd8e6" stroke-dasharray="4 4"/></svg>
  <svg class="abs" style="left:646px;top:114px" width="72" height="270" viewBox="0 0 72 270">
    <g fill="#33a6d7"><circle cx="36" cy="36" r="34" fill="#d3eaf5"/><circle cx="36" cy="36" r="27"/><circle cx="36" cy="132" r="34" fill="#d3eaf5"/><circle cx="36" cy="132" r="27"/><circle cx="36" cy="229" r="34" fill="#d3eaf5"/><circle cx="36" cy="229" r="27"/></g>
    <g fill="none" stroke="#fff" stroke-width="2.5"><circle cx="36" cy="30" r="6"/><path d="M25 46c2-8 20-8 22 0"/><path d="M26 132l7 7 13-14"/><circle cx="36" cy="226" r="9"/><path d="M27 238h18"/></g>
  </svg>
  <div class="reason" style="top:130px"><h4>EXPERIENCE COUNTS</h4><p>We have a team of nationally trained and qualified Refrigeration/HVAC/Electrical Engineers and...<b>[+]</b></p></div>
  <div class="reason" style="top:222px"><h4>SATISFACTION GUARANTEE</h4><p>We aim to please and I put my name behind our brand! We will take care of your project from... <b>[+]</b></p></div>
  <div class="reason" style="top:315px"><h4>LOW PRESSURE SALES</h4><p>Nobody likes the vacuum salesmen's techniques and neither do we. We will come to your home.... <b>[+]</b></p></div>
</section>

<h2 class="section-title" style="top:2283px">BRANDS WE <span>SERVE</span></h2>
<svg class="divider" style="top:2333px" viewBox="0 0 516 20"><line x1="0" y1="10" x2="238" y2="10" stroke="#c8c8c8"/><line x1="278" y1="10" x2="516" y2="10" stroke="#c8c8c8"/><circle cx="258" cy="10" r="8" fill="none" stroke="#c8c8c8" stroke-width="2" stroke-dasharray="3 2"/></svg>
<svg class="abs" style="left:38px;top:2414px" width="20" height="34" viewBox="0 0 20 34"><path d="M16 3L4 17l12 14" fill="none" stroke="#c4c4c4" stroke-width="2.5"/></svg>
<svg class="abs" style="left:1142px;top:2414px" width="20" height="34" viewBox="0 0 20 34"><path d="M4 3l12 14L4 31" fill="none" stroke="#c4c4c4" stroke-width="2.5"/></svg>
<div class="brand-box" style="left:80px">Nordavel</div>
<div class="brand-box" style="left:257px">Korrowane</div>
<div class="brand-box" style="left:434px">Pelnor</div>
<div class="brand-box" style="left:612px">Veltrada</div>
<div class="brand-box" style="left:789px">Talvoro</div>
<div class="brand-box" style="left:968px">Osmelo</div>

<section class="newsletter">
  <svg class="abs" style="left:112px;top:13px" width="52" height="52" viewBox="0 0 52 52"><circle cx="26" cy="26" r="24" fill="none" stroke="#fff" stroke-width="2.5"/><rect x="14" y="18" width="24" height="16" fill="#fff"/><path d="M14 18l12 9 12-9" fill="none" stroke="#2b80b0" stroke-width="2"/></svg>
  <h5>Sign Up For Newsletter</h5>
  <div class="news-input">Enter your email here</div>
  <div class="news-btn">SUBSCRIBE</div>
</section>

<footer class="site-footer">
  <div class="foot-title" style="left:82px">QUICK <span>LINKS</span></div><div class="foot-rule" style="left:82px"></div>
  <ul class="foot-list" style="left:84px"><li class="active">Home</li><li>About Us</li><li>Services</li><li>Gallery</li><li>Contact Us</li></ul>

  <div class="foot-title" style="left:321px">CONTACT <span>DETAILS</span></div><div class="foot-rule" style="left:321px"></div>
  <div class="foot-contact">
    <div style="color:#fff;font-weight:700">BRAMBLE WORKS</div>
    <div>27 Harlow Crescent Petone, Wellington</div>
    <div class="row"><svg width="14" height="14" viewBox="0 0 24 24"><path d="M6.6 10.8a15 15 0 0 0 6.6 6.6l2.2-2.2a1 1 0 0 1 1-.25 11.4 11.4 0 0 0 3.6.57 1 1 0 0 1 1 1V20a1 1 0 0 1-1 1A17 17 0 0 1 3 4a1 1 0 0 1 1-1h3.5a1 1 0 0 1 1 1c0 1.25.2 2.45.57 3.6a1 1 0 0 1-.25 1z" fill="#33a6d7"/></svg>022 481 3906</div>
    <div class="row"><svg width="14" height="14" viewBox="0 0 24 24"><rect x="4" y="8" width="16" height="10" fill="#33a6d7"/><rect x="7" y="4" width="10" height="5" fill="#33a6d7"/></svg>022 481 3906</div>
    <div class="row"><svg width="14" height="14" viewBox="0 0 24 24"><rect x="3" y="6" width="18" height="12" fill="#33a6d7"/></svg>Marta.k@bramwks.co.nz</div>
  </div>

  <div class="foot-title" style="left:668px">QUICK <span>INQUIRY</span></div><div class="foot-rule" style="left:668px"></div>
  <div class="field" style="top:86px">Name</div>
  <div class="field" style="top:120px">Email</div>
  <div class="field" style="top:154px">Message</div>
  <div class="btn" style="left:668px;top:193px;width:106px;height:30px;line-height:30px;font-size:15px">Submit</div>

  <div class="foot-title" style="left:1005px">FOLLOW <span>US</span></div><div class="foot-rule" style="left:1005px;width:90px"></div>
  <div class="social" style="top:96px"><i></i>FRIENDLOOP</div>
  <div class="social" style="top:148px"><i></i>CHIRPLINE</div>
  <div class="social" style="top:200px"><i></i>WORKWEAVE</div>
</footer>
<div class="copyright">Copyright © 2016 BRAMBLE WORKS. All Rights Reserved.</div>

</body>
</html>
```